Etiketten für Imkerei mit Spezialisierung auf Bio Lagenhonig
Zielgruppe
wiesfalter.at - BioImkerei Lindorf
Kleine Nebenerwerbs Imkerei mit Spezialisierung auf Bio Lagenhonig (nähere Infos sind auf der Website nachzulesen)
Als weitere Produktlinie bieten wir Honig+ / Honig mit Zutaten wie Himbeer, Erdbeer, Haselnuss, Mohn, Ingwer, Thymian, usw an.
Zielgruppe: Personen die offen für die Vielfalt der Natur sind, gesunde und natürliche Lebensmittel lieben und die bereit sind die aufwändige, großteils manuelle, Arbeit entsprechend zu entlohnen.
Gesucht:
ÄNDERUNG: Da die Anforderung für das ausgesetzte Preisgeld offensichtlich zu komplex ist, reduziere ich die Anforderung auf Etiketten für die Produktserie Honig+, Gesamtkonzepte sind nicht erforderlich werden aber gerne angenommen.
ÜRSPRÜNGLICH:
Redesign der aktuellen Honigetiketten
Basisdesign für Lagenhonig und Honig+ das entsprechende Varianten zulässt.
Aufgabenstellung
Ich wünsche mir ein modernes, edles (oder Öko look) Design mit sehr guten Wiedererkennungswert das sich von gängigen Honigetiketten deutlich abhebt.
Das wiesfalter Logo soll enthalten sein kann aber bei Bedarf angepasst werden (z.B. monocrome Verison)
Für Lagenhonig werden derzeit 400g und 100g Gläser mit hohem schwarzen DrehKap Decke und,
für Honig+ 250g und 100g mit hohem silbenen DrehKap Deckel verwendet. Beispiele sind im Webshop unter https://solvenhof.at/index.php/wiesfalter ersichtilich.
Für das Ablaufdatum ist evtl. ein Feld für manuelle Stempelung vorzusehen.
Bitte die Sichtfeldregelung der EU Verpackungsverordnung einhalten.
Bisherige Etiketten hatten den Anspruch das diese auf guten Laserdruckern ausdruckbar waren - das ist jetzt nicht mehr zwingend notwendig (wäre für Kleinauflagen aber trotzdem vorteilhaft)

```html
<!DOCTYPE html>
<html lang="de">
<head>
<meta charset="utf-8">
<title>Honig+ Johannisbeere – Etikett</title>
<link rel="stylesheet" href="https://fonts.googleapis.com/css2?family=Source+Sans+3:wght@400;600;700&family=Allura&display=swap">
<style>
  :root{
    --bg:#ffffff;
    --orange-deep:#ef6410;
    --orange:#f68a1e;
    --amber:#f9ae34;
    --amber-light:#fbc86a;
    --white:#ffffff;
    --white-soft:rgba(255,255,255,.82);
    --bio-green:#7fb92c;
    --bio-green-text:#6aa62a;
  }
  *{box-sizing:border-box;margin:0;padding:0}
  html,body{width:1130px;height:1200px;overflow:hidden;background:var(--bg)}
  body{position:relative;font-family:"Source Sans 3",sans-serif;color:var(--white)}

  .label-panel{
    position:absolute;width:480px;height:300px;border-radius:26px;overflow:hidden;
    background:linear-gradient(90deg,var(--orange-deep) 0%,var(--orange) 45%,var(--amber) 80%,var(--amber-light) 100%);
  }
  .label-panel::after{
    content:"";position:absolute;inset:0;
    background:linear-gradient(180deg,rgba(255,255,255,.08) 0%,rgba(255,255,255,0) 50%,rgba(230,80,0,.18) 100%);
  }
  .panel-front{left:70px;top:220px}
  .panel-storage{left:580px;top:220px}
  .panel-ingredients{left:70px;top:780px}
  .panel-producer{left:580px;top:780px}

  .abs{position:absolute;z-index:1}
  .rule{position:absolute;height:2px;background:var(--white-soft);z-index:1}

  /* front */
  .series-name{left:28px;top:46px;font-size:21px;font-weight:600;letter-spacing:.2px}
  .series-name sup{font-size:14px;vertical-align:8px}
  .rule-top{left:14px;top:80px;width:408px}
  .product-title{left:0;width:100%;top:92px;text-align:center;font-family:"Allura",cursive;font-size:72px;line-height:1;padding-right:40px}
  .product-sub{left:0;width:100%;top:170px;text-align:center;font-size:17px;letter-spacing:.3px;padding-right:30px}
  .rule-bottom{left:14px;top:252px;width:230px}
  .front-web{left:28px;top:262px;font-size:15px}
  .brand-name{right:44px;top:248px;font-size:32px;font-weight:700;letter-spacing:.5px}

  /* storage / certification */
  .net-weight{font-size:24px;font-weight:700}
  .panel-storage .net-weight{left:310px;top:60px}
  .storage-note{left:132px;top:116px;font-size:13px;line-height:1.15}
  .cert-badge{left:132px;top:152px;width:144px;height:94px;background:var(--bio-green)}
  .cert-code{left:290px;top:168px;font-size:17px;line-height:1}
  .cert-origin{left:290px;top:188px;font-size:11px}
  .bio-word{left:288px;top:200px;font-size:44px;color:var(--bio-green-text);line-height:1}

  /* ingredients */
  .panel-ingredients .net-weight{left:14px;top:84px}
  .ingr-block{left:140px;top:84px;width:300px}
  .ingr-title{font-size:25px;font-weight:700;line-height:1.1}
  .ingr-lead{font-size:14.5px;line-height:1.1;margin-top:4px}
  .ingr-head{font-size:15px;font-weight:700;margin-top:14px}
  .ingr-list{font-size:14.5px;line-height:1.1}
  .ingr-note{font-size:11.5px;line-height:1.2;margin-top:2px}

  /* producer */
  .producer{left:0;width:100%;top:78px;text-align:center;padding-right:50px;font-size:14px;line-height:1.15}
  .producer-name{font-size:17px;font-weight:600}
  .producer-web{margin-top:16px;font-size:16px;font-weight:700;letter-spacing:.4px}
  .best-before{left:120px;top:244px;font-size:12.5px;line-height:1.15}
  .stamp-field{left:200px;top:234px;width:140px;height:70px}
  .stamp-date{left:200px;top:262px;width:140px;text-align:center;font-size:14px;color:#333}
</style>
</head>
<body>

<section class="label-panel panel-front" aria-label="Vorderseite">
  <div class="abs series-name">HONIG<sup>+</sup></div>
  <div class="rule rule-top"></div>
  <div class="abs product-title">Johannesbeere</div>
  <div class="abs product-sub">Feinste Komposition mit Honig</div>
  <div class="rule rule-bottom"></div>
  <div class="abs front-web">www.wiesfalter.at</div>
  <div class="abs brand-name">wiesfalter</div>
</section>

<section class="label-panel panel-storage" aria-label="Lagerung und Zertifizierung">
  <div class="abs net-weight">250 g</div>
  <div class="abs storage-note">vor Wärme geschützt<br>und trocken lagern</div>
  <div class="abs cert-badge" role="img" aria-label="Bio-Zertifizierungszeichen"></div>
  <div class="abs cert-code">AT-BIO-917</div>
  <div class="abs cert-origin">EU-Landwirtschaft</div>
  <div class="abs bio-word">BIO</div>
</section>

<section class="label-panel panel-ingredients" aria-label="Zutaten">
  <div class="abs net-weight">250 g</div>
  <div class="abs ingr-block">
    <div class="ingr-title">Honigkomposition</div>
    <div class="ingr-lead">mit österreichischem Blütenhonig<br>aus biologischer Bienenhaltung</div>
    <div class="ingr-head">Zutaten</div>
    <div class="ingr-list">95% Blütenhonig aus kontrolliert<br>biologischer Landwirtschaft,<br>5% Johannisbeerpulver</div>
    <div class="ingr-note">(gefriergetrocknet, entspricht 45%<br>Frischfruchtanteil)</div>
  </div>
</section>

<section class="label-panel panel-producer" aria-label="Hersteller und Haltbarkeit">
  <div class="abs producer">
    <div class="producer-name">Bio Imkerei Lindorf</div>
    <div>Föhrenweg 14</div>
    <div>3592 Altenau am Fluss</div>
    <div class="producer-web">www.wiesfalter.at</div>
  </div>
  <div class="abs best-before">Mindestens<br>haltbar bis:</div>
  <svg class="abs stamp-field" viewBox="0 0 140 70" aria-hidden="true">
    <path d="M0 70 A70 60 0 0 1 140 70 Z" fill="#ffffff"/>
  </svg>
  <div class="abs stamp-date">30.06.2019</div>
</section>

</body>
</html>
```